lantern pathway for children needs a website designer

We need a website designer for our new extension to our company known as 'lantern pathway' providing shadow support services to children based in Singapore. We are a sister branch of a private clinic 'Bright horizons' providing speech language, occupational, and educational therapy to children.

We would like to use our own photos. So the selected design should have a frame with pictures to give us an idea but we will replace them with our own. We will be needing help with inputting information and changing information throughout.

We would like to see designs that are simple, and professional. We have a logo (see attached). The result should convey professionalism in shadow support, fostering independent thinking and moving students towards self-learning.

Target Market(s)

Teachers, psychologists, parents

Industry/Entity Type

Clinic

Requirements
Should not have
• too distracting colours

```html
<!DOCTYPE html>
<html lang="en">
<head>
<meta charset="utf-8">
<title>Lantern Pathway</title>
<link href="https://fonts.googleapis.com/css2?family=Arimo:wght@400;700&family=Oswald:wght@500&display=swap" rel="stylesheet">
<style>
:root{
  --ink:#1f1f1f;
  --muted:#3a3a3a;
  --red:#b01c1c;
  --red-soft:#c9474a;
  --bar:#2c2c2c;
  --page:#f3f3f3;
  --band:#ebebeb;
  --line:#dcdcdc;
  --footer:#4b4b4b;
  --white:#fff;
}
*{margin:0;padding:0;box-sizing:border-box}
html,body{width:900px;height:1200px;overflow:hidden}
body{position:relative;background:var(--page);font-family:"Arimo",Arial,sans-serif;color:var(--ink)}
.abs{position:absolute}

.topnav{left:0;top:0;width:900px;height:31px;background:var(--bar)}
.home-btn{left:93px;top:4px;width:23px;height:23px;border-radius:50%;background:#111;border:1px solid #555}
.topnav ul{list-style:none;position:absolute;left:126px;top:0;display:flex;height:31px}
.topnav li{color:#eee;font-size:10.4px;line-height:31px;padding:0 13.5px;border-right:1px solid #3d3d3d}
.topnav li:last-child{border:none}

.brand{left:92px;top:66px;font-size:27px;font-weight:700;color:var(--red);display:flex;align-items:center;gap:8px;letter-spacing:-.3px}
.brand-mark{width:14px;height:14px;background:var(--red)}
.contact{left:465px;top:56px;font-size:10.6px;color:var(--muted);display:flex;gap:12px;align-items:center}
.contact b{color:var(--ink)}
.search{left:630px;top:82px;width:182px;height:32px;border:1px solid var(--line);border-radius:4px;background:#f7f7f7}
.search-field{position:absolute;left:5px;top:4px;width:148px;height:22px;border:1px solid #d2d2d2;border-radius:8px;background:var(--white);font-size:9px;color:#888;padding:6px 8px;letter-spacing:.3px}
.search svg{position:absolute;right:9px;top:9px}

.hero{left:92px;top:131px;width:720px;height:272px;background:linear-gradient(#b3b3b3,#a2a2a2)}
.hero-frame{left:24px;top:39px;width:339px;height:204px;background:var(--white);box-shadow:0 3px 8px rgba(0,0,0,.35)}
.hero-photo{left:8px;top:7px;width:324px;height:190px;background:linear-gradient(90deg,#8d8d8d,#6c6c6c 60%,#555)}
.play{left:137px;top:72px}
.hero-copy{left:394px;top:38px;width:310px;color:var(--white)}
.hero-copy h2{font-size:17.6px;font-weight:700;margin-bottom:12px;color:#f6f6f6}
.hero-copy p{font-size:8.8px;line-height:16px;color:#202020;margin-bottom:6px}
.hero-copy ul{list-style:none}
.hero-copy li{font-size:8.8px;line-height:22.5px;color:#202020;display:flex;align-items:center;gap:9px}
.btn{background:var(--red);color:var(--white);font-size:13px;text-align:center;border-radius:2px}
.learn{left:395px;top:209px;width:99px;height:30px;line-height:30px}

.tabs{left:92px;top:403px;width:720px;height:40px;background:linear-gradient(#4a4a4a,#2e2e2e);box-shadow:0 8px 10px -6px rgba(0,0,0,.45)}
.pager{left:14px;top:8px;display:flex;border:1px solid #222}
.pager span{width:27px;height:23px;line-height:23px;text-align:center;font-size:10px;color:#999;background:#3a3a3a;border-right:1px solid #252525}
.pager span.on{color:#fff;background:#2a2a2a}
.tab{top:0;height:40px;line-height:40px;text-align:center;font-family:"Oswald",sans-serif;font-size:15.5px;color:#8a8a8a;border-left:1px solid #222}
.tab.on{color:#fff;background:#262626}

.welcome{left:92px;top:472px;width:720px;text-align:center}
.welcome h1{font-size:14px;font-weight:400;margin-bottom:14px}
.welcome p{font-size:8.8px;line-height:16.6px;color:var(--muted)}

.services{left:0;top:575px;width:900px;height:233px;background:var(--band)}
.service{top:16px;width:256px;text-align:center}
.service .icon-box{margin:0 auto;width:94px;height:77px;border:2px solid var(--red);background:var(--white);display:flex;align-items:center;justify-content:center}
.icon-fill{width:60px;height:50px;background:#d8d8d8}
.service h3{font-size:14px;font-weight:400;margin:14px 0 8px}
.service p{font-size:8.8px;line-height:16.6px;color:var(--muted)}
.service .btn{margin:10px auto 0;width:72px;height:31px;line-height:31px}

.support{left:92px;top:834px;width:514px;height:276px;background:var(--white)}
.support h4{position:absolute;left:13px;top:20px;font-size:13.6px;font-weight:400}
.support .rule{position:absolute;left:137px;top:31px;width:360px;height:5px;background:repeating-linear-gradient(90deg,#ddd 0 1px,transparent 1px 2px)}
.faq{position:absolute;left:13px;width:485px;border:1px solid #e6e6e6}
.faq .q{display:flex;align-items:center;height:24px;font-size:10.4px}
.faq .plus{width:26px;height:24px;background:var(--red);color:#fff;text-align:center;line-height:24px;font-size:12px;margin-right:15px}
.faq .a{font-size:8.8px;line-height:16.4px;color:var(--muted);padding:6px 10px 8px 15px}

.appt{left:622px;top:834px;width:190px;height:276px;background:#ececec}
.appt-head{height:74px;background:var(--red-soft);color:var(--white);text-align:center;padding-top:14px}
.appt-head .t{font-size:13.6px}
.appt-head .ph{font-size:13.6px;margin-top:8px;display:flex;justify-content:center;align-items:center;gap:10px}
.or{position:absolute;left:83px;top:66px;width:26px;height:16px;background:#ececec;border-radius:8px 8px 0 0;text-align:center;font-size:10px;line-height:18px}
.field{position:absolute;left:16px;width:164px;height:24px;border:1px solid #d4d4d4;background:var(--white);font-size:9px;color:#999;padding:6px 7px;box-shadow:inset 0 1px 2px rgba(0,0,0,.08)}
.submit{position:absolute;left:76px;top:254px;width:53px;height:25px;background:#e2e2e2;border-bottom:2px solid var(--red);font-size:10.4px;text-align:center;line-height:24px;border-radius:2px}

.footer{left:0;top:1131px;width:900px;height:69px;background:var(--footer)}
.footer .brand{top:20px;font-size:22px;color:#e8e8e8}
.footer .brand-mark{background:#e8e8e8}
.copy{left:340px;top:32px;font-size:8.8px;color:#e6e6e6}
.social{left:677px;top:25px;display:flex;gap:7px}
.social span{width:20px;height:20px;border-radius:50%;background:#d9d9d9;border:2px solid #777}
</style>
</head>
<body>

<nav class="topnav abs">
  <div class="home-btn abs"><svg width="21" height="21" viewBox="0 0 21 21"><path d="M5 11 10.5 6 16 11M7 10v5h7v-5" fill="#fff"/></svg></div>
  <ul><li>ABOUT US</li><li>MISSION</li><li>OUR SERVICES</li><li>SHADOW SUPPORT</li><li>FOR REFERRERS</li></ul>
</nav>

<div class="brand abs"><span class="brand-mark"></span>Lantern Pathway</div>
<div class="contact abs">
  <span>Help Line &nbsp;: &nbsp;<b>+65 6100 2480</b></span>
  <svg width="13" height="9" viewBox="0 0 13 9"><rect width="13" height="9" fill="#222"/><path d="M0 0 6.5 5 13 0" stroke="#fff" fill="none"/></svg>
  <span>enquiries@corvalelearning.sg</span>
</div>
<div class="search abs">
  <div class="search-field">SEARCH</div>
  <svg width="14" height="14" viewBox="0 0 14 14"><circle cx="5.5" cy="5.5" r="4.3" stroke="#555" stroke-width="2" fill="none"/><path d="M8.7 8.7 13 13" stroke="#555" stroke-width="2.4"/></svg>
</div>

<section class="hero abs">
  <div class="hero-frame abs">
    <div class="hero-photo abs" role="img" aria-label="Photo of a child speaking, letters floating from the mouth"></div>
    <svg class="play abs" width="50" height="50" viewBox="0 0 50 50"><circle cx="25" cy="25" r="24" fill="rgba(255,255,255,.55)"/><path d="M21 17l10 8-10 8z" fill="#222"/></svg>
  </div>
  <div class="hero-copy abs">
    <h2>Lantern Pathway is part</h2>
    <p>Lorem ipsum dolor sit amet, consectetur adipiscing elit. Vivamus leo ante, consectetur sit amet vulputate vel, dapibus sit amet lectus.</p>
    <ul>
      <li><svg width="9" height="9" viewBox="0 0 9 9"><circle cx="4.5" cy="4.5" r="4.5" fill="#fff"/><path d="M2.3 4.6l1.5 1.4 2.9-3" stroke="#333" fill="none"/></svg>Train shadows with a strong focus on equipping them with dynamic.</li>
      <li><svg width="9" height="9" viewBox="0 0 9 9"><circle cx="4.5" cy="4.5" r="4.5" fill="#fff"/><path d="M2.3 4.6l1.5 1.4 2.9-3" stroke="#333" fill="none"/></svg>Goals set out by professionals will be supported</li>
      <li><svg width="9" height="9" viewBox="0 0 9 9"><circle cx="4.5" cy="4.5" r="4.5" fill="#fff"/><path d="M2.3 4.6l1.5 1.4 2.9-3" stroke="#333" fill="none"/></svg>Frequent feedback and updates will be provided</li>
      <li><svg width="9" height="9" viewBox="0 0 9 9"><circle cx="4.5" cy="4.5" r="4.5" fill="#fff"/><path d="M2.3 4.6l1.5 1.4 2.9-3" stroke="#333" fill="none"/></svg>Train shadows with a strong focus on equipping</li>
    </ul>
  </div>
  <div class="btn learn abs">Learn More</div>
</section>

<div class="tabs abs">
  <div class="pager abs"><span>&#8249;</span><span class="on">1</span><span>2</span><span>3</span><span>&#8250;</span></div>
  <div class="tab on abs" style="left:164px;width:166px">LANGUAGE THERAPY</div>
  <div class="tab abs" style="left:330px;width:199px">OCCUPATIONAL THERAPY</div>
  <div class="tab abs" style="left:529px;width:191px">EDUCATIONAL THERAPY</div>
</div>

<section class="welcome abs">
  <h1>Welcome To Our Company</h1>
  <p>Lantern Pathway is part of the Corvale Learning Group of Companies, who are providing speech language therapy, occupational therapy and educational therapy services<br>to both the Singapore and the international school community. &nbsp;Lantern Pathway aims to work in an integrated manner, respecting the work of the respective professionals<br>involved and collaborating effectively.</p>
</section>

<section class="services abs">
  <div class="service abs" style="left:67px">
    <div class="icon-box"><div class="icon-fill" role="img" aria-label="Icon of a group with a speech bubble"></div></div>
    <h3>Language Therapy</h3>
    <p>Lorem ipsum dolor sit amet, consectetuer adipiscing<br>elit, sed diam nonummy nibh euismod tincidunt ut<br>laoreet dolore magna aliquam erat volutpat.</p>
    <div class="btn">More..</div>
  </div>
  <div class="service abs" style="left:323px">
    <div class="icon-box"><div class="icon-fill" role="img" aria-label="Icon of a seated person"></div></div>
    <h3>Occupational Therapy</h3>
    <p>Lorem ipsum dolor sit amet, consectetuer adipiscing<br>elit, sed diam nonummy nibh euismod tincidunt ut<br>laoreet dolore magna aliquam erat volutpat.</p>
    <div class="btn">More..</div>
  </div>
  <div class="service abs" style="left:581px">
    <div class="icon-box"><div class="icon-fill" role="img" aria-label="Icon of an open book"></div></div>
    <h3>Educational Therapy</h3>
    <p>Lorem ipsum dolor sit amet, consectetuer adipiscing<br>elit, sed diam nonummy nibh euismod tincidunt ut<br>laoreet dolore magna aliquam erat volutpat.</p>
    <div class="btn">More..</div>
  </div>
</section>

<section class="support abs">
  <h4>Shadow Support</h4>
  <div class="rule"></div>
  <div class="faq" style="top:59px">
    <div class="q"><span class="plus">+</span>What is shadow support?</div>
    <p class="a">A shadow support is para-professional who can help a struggling student to integrate and learn in their school envi-<br>ronment. &nbsp;&nbsp;At different points in a student’s life, there may be a need for a para-professional who could step in to help<br>make a difference</p>
  </div>
  <div class="faq" style="top:156px"><div class="q"><span class="plus">+</span>What are its Advantages?</div></div>
  <div class="faq" style="top:194px"><div class="q"><span class="plus">+</span>How do I know if my child needs shadowing</div></div>
  <div class="faq" style="top:232px"><div class="q"><span class="plus">+</span>What are its Advantages?</div></div>
</section>

<aside class="appt abs">
  <div class="appt-head">
    <div class="t">Make an Appointment</div>
    <div class="ph"><svg width="20" height="20" viewBox="0 0 20 20"><circle cx="10" cy="10" r="10" fill="#fff"/><path d="M7 5l2 2.5-1.2 1.3c.7 1.5 1.8 2.6 3.3 3.3l1.3-1.2L15 13l-1.5 2C9 14.5 5.5 11 5 6.5z" fill="#222"/></svg>+65 6100 2480</div>
  </div>
  <div class="or">OR</div>
  <div class="field" style="top:95px">Full Name</div>
  <div class="field" style="top:132px">Phone</div>
  <div class="field" style="top:170px">Email</div>
  <div class="field" style="top:208px;height:30px;padding-top:9px">Message</div>
  <div class="submit">Submit</div>
</aside>

<footer class="footer abs">
  <div class="brand abs"><span class="brand-mark"></span>Lantern Pathway</div>
  <div class="copy abs">© Copyright 2014. All Rights Reserved by Lantern Pathway</div>
  <div class="social abs"><span></span><span></span><span></span><span></span><span></span></div>
</footer>

</body>
</html>
```